Tech business card design

We need an amazing business card design for our new business 'Pexla' a marketing tech startup based in Sydney, Australia. We provide an online marketplace for businesses to search and buy advertising media, connect with service providers and learn more about marketing. We wish to communicate 'cool tech', reliability and professionalism and design based around our logo.

Target Market(s)

Business Owners

Contact Information for Business Card

Name
Position
Email Address
Website
Phone Number

Font styles to use
Other font styles liked:
• Avenir & Avenir Next

Colors

Designer to choose colors to be used in the design.

```html
<!DOCTYPE html>
<html lang="en">
<head>
<meta charset="utf-8">
<title>Pexla Business Card</title>
<link rel="stylesheet" href="https://fonts.googleapis.com/css2?family=Lato:wght@400;700;900&display=swap">
<style>
  :root {
    --page-bg: #e9e9ec;
    --card-navy: #0c0c3a;
    --card-panel: #20244c;
    --circle-white: #f4f4f6;
    --text-white: #ffffff;
    --brand-navy: #14163f;
  }
  * { box-sizing: border-box; margin: 0; padding: 0; }
  html, body { width: 1200px; height: 900px; overflow: hidden; }
  body {
    background: var(--page-bg);
    font-family: "Lato", sans-serif;
    position: relative;
  }
  .business-card {
    position: absolute;
    left: 150px;
    top: 171px;
    width: 900px;
    height: 558px;
    background: var(--card-navy);
    overflow: hidden;
    box-shadow: 0 12px 40px rgba(0,0,0,0.18);
  }
  .side-panel {
    position: absolute;
    left: 609px;
    top: 0;
    width: 291px;
    height: 100%;
    background: var(--card-panel);
  }
  .brand-circle {
    position: absolute;
    left: 371px;
    top: 39px;
    width: 480px;
    height: 480px;
    border-radius: 50%;
    background: var(--circle-white);
    display: flex;
    align-items: center;
    justify-content: center;
  }
  .brand-name {
    font-family: "Lato", sans-serif;
    font-weight: 900;
    font-size: 120px;
    letter-spacing: -2px;
    color: var(--brand-navy);
    line-height: 1;
  }
  .holder {
    position: absolute;
    left: 52px;
    top: 70px;
    color: var(--text-white);
  }
  .holder-name {
    font-weight: 900;
    font-size: 28px;
    letter-spacing: 0.5px;
    line-height: 1.1;
  }
  .holder-role {
    font-weight: 400;
    font-size: 23px;
    margin-top: 4px;
  }
  .contact-list {
    position: absolute;
    left: 52px;
    top: 386px;
    list-style: none;
    color: var(--text-white);
    font-size: 23px;
    line-height: 33px;
  }
  .contact-item { display: flex; align-items: center; gap: 10px; }
  .contact-icon { width: 18px; height: 18px; fill: var(--text-white); flex: none; }
</style>
</head>
<body>
  <div class="business-card">
    <div class="side-panel"></div>
    <div class="brand-circle">
      <span class="brand-name">pexla</span>
    </div>
    <div class="holder">
      <div class="holder-name">MARCUS REED</div>
      <div class="holder-role">Managing Director</div>
    </div>
    <ul class="contact-list">
      <li class="contact-item">
        <svg class="contact-icon" viewBox="0 0 20 20" aria-hidden="true">
          <path d="M2 7c0-2 3.5-4 8-4s8 2 8 4v1.5h-4V6.5c-1.2-.5-2.6-.7-4-.7s-2.8.2-4 .7v2H2z"/>
          <path d="M4 10l2-2h8l2 2v7H4z"/>
        </svg>
        <span>044-987 654 321</span>
      </li>
      <li class="contact-item">
        <svg class="contact-icon" viewBox="0 0 20 20" aria-hidden="true">
          <path d="M2 4h16v12H2z M3.5 5.5v.6L10 11l6.5-4.9v-.6z" fill-rule="evenodd"/>
        </svg>
        <span>hello@pexlamail.com</span>
      </li>
      <li class="contact-item">
        <svg class="contact-icon" viewBox="0 0 20 20" aria-hidden="true">
          <circle cx="10" cy="10" r="8"/>
          <path d="M6 6c2 0 3 1 3 2.5S7 10 7.5 12 9 14 8.5 16.5M13 4.5c-1 1.5 0 2.5 1.5 3s2 2 1 4" stroke="#0c0c3a" stroke-width="1.4" fill="none"/>
        </svg>
        <span>www.pexlasite.com</span>
      </li>
    </ul>
  </div>
</body>
</html>
```